Beauty Product Packaging (Ponytail)

I need a packaging design that I have already created but need it print ready and aligned properly. The original file is attached the (Clip in hair) I need the rest of the files laid out.
1. Ponytail Packaging
The layout has already been done it just needs to be aligned, which I cannot figure out how to do. Also the picture of the girl on the front of the package needs to change with each packaging.
13.5 x 17.5 add 3mm bleed
Industry/Entity Type
Hair
Font styles to use
Sans Serif

```html
<!DOCTYPE html>
<html lang="en">
<head>
<meta charset="utf-8">
<title>Lumira Brands – Clip-On Ponytail Packaging</title>
<link rel="stylesheet" href="https://fonts.googleapis.com/css2?family=Mulish:wght@700;800&family=Questrial&display=swap">
<style>
  :root {
    --pink: #ff3fb3;
    --frame-pink: #ffb3dd;
    --white: #ffffff;
    --hair-light: #e6d3a8;
    --hair-mid: #c4a672;
    --hair-dark: #8e7248;
    --upc-text: #ff3fb3;
  }
  * { margin: 0; padding: 0; box-sizing: border-box; }
  html, body { width: 891px; height: 1200px; overflow: hidden; background: var(--pink); }
  .package {
    position: relative;
    width: 891px;
    height: 1200px;
    background: var(--pink);
    color: var(--white);
    font-family: "Questrial", "Century Gothic", sans-serif;
  }
  .hang-hole { position: absolute; left: 430px; top: 28px; }
  .brand-name {
    position: absolute;
    left: 556px;
    top: 92px;
    font-family: "Mulish", sans-serif;
    font-weight: 800;
    font-size: 50px;
    line-height: 1;
    letter-spacing: -0.5px;
    color: var(--white);
  }
  .kit-label {
    position: absolute;
    left: 55px;
    top: 242px;
    font-family: "Mulish", sans-serif;
    font-weight: 800;
    font-size: 22px;
  }
  .product-frame {
    position: absolute;
    left: 55px;
    top: 297px;
    width: 257px;
    height: 510px;
    background: var(--frame-pink);
    padding: 14px 17px;
  }
  .product-photo {
    width: 100%;
    height: 100%;
    background: linear-gradient(170deg, var(--hair-light) 0%, var(--hair-mid) 45%, var(--hair-dark) 70%, var(--hair-light) 100%);
  }
  .details {
    position: absolute;
    left: 360px;
    width: 480px;
    font-size: 24px;
    line-height: 26px;
  }
  .details h2 {
    font-family: "Mulish", sans-serif;
    font-weight: 800;
    font-size: 25px;
    line-height: 28px;
  }
  .kit-contents { top: 247px; }
  .application { top: 326px; }
  .removal { top: 523px; }
  .dos { top: 692px; }
  .donts { top: 951px; }
  .care { top: 1030px; }
  .online {
    position: absolute;
    left: 55px;
    top: 826px;
  }
  .online h2 {
    font-family: "Mulish", sans-serif;
    font-weight: 800;
    font-size: 26px;
    line-height: 32px;
  }
  .online p { font-size: 25px; line-height: 30px; }
  .social { position: absolute; left: 58px; top: 913px; }
  .origin {
    position: absolute;
    left: 55px;
    top: 980px;
    font-size: 13px;
  }
  .upc-box {
    position: absolute;
    left: 55px;
    top: 1002px;
    width: 252px;
    height: 141px;
    background: var(--white);
    display: flex;
    align-items: center;
    justify-content: center;
    font-family: "Mulish", sans-serif;
    font-weight: 800;
    font-size: 26px;
    color: var(--upc-text);
  }
</style>
</head>
<body>
<main class="package">
  <svg class="hang-hole" width="28" height="28" viewBox="0 0 28 28" aria-hidden="true">
    <circle cx="14" cy="14" r="11.5" fill="none" stroke="#ffffff" stroke-width="2"/>
  </svg>

  <div class="brand-name">Lumira Brands</div>

  <div class="kit-label">Clip-On Kit Includes :</div>
  <div class="product-frame">
    <div class="product-photo" role="img" aria-label="Product photo of a wavy blonde clip-on ponytail"></div>
  </div>

  <section class="details kit-contents">
    <p>1Clip-on Ponytail<br>High Fiber Hair</p>
  </section>

  <section class="details application">
    <h2>Application Instructions:</h2>
    <p>Sweep all hair into a ponytail with hair tie.<br>Attach hook inside your own ponytail.<br>Wrap around attachment to secue.</p>
  </section>

  <section class="details removal">
    <h2>Removal Instructions:</h2>
    <p>Unrap attachment, unhook ponytail.<br>Brush out and store in ponytail pouch.</p>
  </section>

  <section class="details dos">
    <h2>Do’s:</h2>
    <p>Brush out ponytail before and after use<br>May use a detangling spray to prevent tangling. May use dry shampoo. May use heat up to 300 degrees farenheit.</p>
  </section>

  <section class="details donts">
    <h2>Dont’s:</h2>
    <p>Wash with regular shampoo. Use heat over 300 degrees farenheit.</p>
  </section>

  <section class="details care">
    <h2>Care</h2>
    <p>Brush before and after use. Store in ponytail pouch to prevent tangling.</p>
  </section>

  <div class="online">
    <h2>Visit us online:</h2>
    <p>lumiraorganics.com</p>
  </div>

  <svg class="social" width="160" height="34" viewBox="0 0 160 34" aria-hidden="true">
    <circle cx="16" cy="17" r="15" fill="#ffffff"/>
    <circle cx="57" cy="17" r="15" fill="#ffffff"/>
    <circle cx="98" cy="17" r="15" fill="#ffffff"/>
    <circle cx="138" cy="17" r="15" fill="#ffffff"/>
  </svg>

  <div class="origin">Made in China</div>
  <div class="upc-box">UPC</div>
</main>
</body>
</html>
```